KPV Datacore Solutions

We need a Logo and Website for our company based in London. We are a IT recruitment company . We provide quality resources to top IT company across UK.

Industry/Entity Type

It Company

Number of Pages Required

4 page

```html
<!DOCTYPE html>
<html lang="en">
<head>
<meta charset="utf-8">
<title>KPV Datacore Solutions</title>
<link href="https://fonts.googleapis.com/css2?family=Open+Sans:wght@400;600;700&family=Raleway:wght@400;500;600;700&display=swap" rel="stylesheet">
<style>
:root{
  --red:#d0342c;
  --red-dark:#b82a23;
  --ink:#2b2b2b;
  --text:#8a8a8a;
  --muted:#a9a9a9;
  --white:#ffffff;
  --night:#1d2a3c;
  --footer:#2b2e3b;
  --footer-bar:#22252f;
  --footer-text:#c9cbd2;
}
*{box-sizing:border-box;margin:0;padding:0}
html,body{width:1200px;height:4091px;overflow:hidden}
body{position:relative;background:var(--white);font-family:"Open Sans",Arial,sans-serif;color:var(--text)}
.block{position:absolute;left:0;width:1200px}
.abs{position:absolute}
.center{text-align:center}
.heading{font-family:"Raleway",Arial,sans-serif;font-weight:600;color:var(--ink);font-size:20px;letter-spacing:3px;text-transform:uppercase;text-align:center}
.rule{width:44px;height:3px;background:var(--red);margin:10px auto 0}
.lead{font-size:13px;line-height:27px;color:var(--text);text-align:center;width:880px;margin:0 auto}
.btn{display:inline-block;background:var(--red);color:var(--white);font-family:"Raleway",Arial,sans-serif;font-weight:700;font-size:13px;letter-spacing:1px;text-transform:uppercase;border-radius:22px;padding:13px 34px}

/* header */
.site-header{top:0;height:68px;background:var(--white);box-shadow:0 1px 4px rgba(0,0,0,.08)}
.brand{left:98px;top:18px;display:flex;align-items:center;gap:12px}
.brand-mark{width:30px;height:30px;background:var(--red)}
.brand-name{font-family:"Raleway",Arial,sans-serif;font-weight:500;font-size:26px;letter-spacing:1px;color:#555;text-transform:uppercase}
.nav a{position:absolute;top:28px;font-family:"Raleway",Arial,sans-serif;font-size:12px;font-weight:600;color:#555;text-decoration:none;letter-spacing:.5px}

/* hero */
.hero{top:68px;height:554px;background:linear-gradient(180deg,#243247 0%,#1e2b3d 45%,#3a3a3c 80%,#4a3a2c 100%)}
.hero-title{top:232px;width:100%;font-family:"Raleway",Arial,sans-serif;font-weight:600;font-size:50px;letter-spacing:5px;color:var(--white);text-transform:uppercase}
.hero-sub{top:300px;width:100%;font-family:"Raleway",Arial,sans-serif;font-weight:500;font-size:22px;letter-spacing:4px;color:var(--white);text-transform:uppercase}
.hero .btn{top:349px;left:502px;padding:13px 30px}

/* welcome */
.welcome{top:686px}
.welcome h1{font-family:"Raleway",Arial,sans-serif;font-weight:700;font-size:26px;letter-spacing:2px;color:var(--red);text-align:center;text-transform:uppercase;margin-bottom:20px}

/* services */
.services{top:870px}
.services .lead{margin-top:30px}
.service{top:150px;width:310px}
.service-photo{width:310px;height:200px}
.service-title{margin-top:22px;font-family:"Raleway",Arial,sans-serif;font-weight:700;font-size:13px;letter-spacing:1.5px;color:var(--ink)}
.service-text{margin-top:6px;font-size:12.5px;line-height:26px;color:var(--text)}

/* what we do */
.whatwedo{top:1404px}
.whatwedo .lead{margin-top:30px}
.feature{top:150px;width:220px;text-align:center}
.feature-icon{width:110px;height:110px;border-radius:50%;background:var(--red);margin:0 auto;display:flex;align-items:center;justify-content:center}
.feature-title{margin-top:24px;font-family:"Raleway",Arial,sans-serif;font-weight:700;font-size:12.5px;letter-spacing:.5px;color:var(--ink);text-transform:uppercase}
.feature-text{margin-top:8px;font-size:12px;line-height:26px;color:var(--text)}

/* about */
.about{top:1860px;height:412px;background:linear-gradient(90deg,#1b2434 0%,#2b3446 40%,#1f2838 70%,#141b27 100%)}
.about .heading{color:var(--white);position:absolute;top:108px;width:100%}
.about .lead{position:absolute;top:156px;left:160px;color:#e5e7ec;width:880px}
.about .btn{top:262px;left:492px}

/* posts */
.posts{top:2340px}
.posts .lead{margin-top:30px}
.post{top:144px;width:480px}
.post-photo{width:224px;height:156px}
.post-body{left:256px;top:0;width:210px}
.post-title{font-family:"Raleway",Arial,sans-serif;font-weight:700;font-size:12.5px;line-height:22px;color:var(--ink);text-transform:uppercase}
.post-date{font-size:11px;color:var(--red);margin-top:2px}
.post-text{margin-top:12px;font-size:12px;line-height:24px;color:var(--text)}
.dots{top:343px;left:583px;display:flex;gap:7px}
.dot{width:7px;height:7px;border-radius:50%;background:#ccc}
.dot.on{background:var(--red)}

/* testimonial */
.testimonial{top:2773px;height:538px;background:linear-gradient(135deg,#c9c2b5 0%,#e8e3da 40%,#9c8e7c 100%)}
.testimonial-panel{left:0;top:0}
.quote-mark{top:96px;left:277px}
.quote{left:90px;top:178px;width:420px;text-align:center;color:var(--white);font-size:12.5px;line-height:28px}
.quote p+p{margin-top:30px}
.quote-author{margin-top:12px;font-weight:700}
.quote-author span{font-weight:400}
.quote-dots{top:470px;left:281px;display:flex;gap:6px}
.quote-dots .dot{background:rgba(255,255,255,.55);width:6px;height:6px}

/* clients */
.clients{top:3387px}
.clients .lead{margin-top:30px}
.client{display:flex;align-items:center;gap:8px;font-family:"Open Sans",Arial,sans-serif;font-weight:600;font-size:27px;color:#a4a4a4}
.client-dot{width:22px;height:22px;border-radius:50%;background:#a4a4a4}

/* footer */
.site-footer{top:3763px;height:268px;background:var(--footer)}
.footer-brand{left:100px;top:78px;width:160px;text-align:center}
.footer-mark{width:40px;height:40px;background:var(--red);margin:0 auto 12px}
.footer-brand-name{font-family:"Raleway",Arial,sans-serif;font-weight:500;font-size:17px;color:var(--white);line-height:24px}
.footer-h{font-family:"Raleway",Arial,sans-serif;font-weight:700;font-size:13px;letter-spacing:1px;color:var(--white);text-transform:uppercase}
.footer-col{top:42px}
.footer-text{margin-top:16px;font-size:11.5px;line-height:25px;color:var(--footer-text)}
.read-more{margin-top:10px;font-size:11px;color:var(--red);display:flex;align-items:center;gap:8px}
.read-more i{display:inline-block;width:12px;height:12px;border-radius:50%;background:var(--red)}
.footer-links{margin-top:14px;list-style:none}
.footer-links li{font-size:11.5px;line-height:27.5px;color:var(--footer-text)}
.map{margin-top:12px;width:186px;height:108px;background:linear-gradient(135deg,#dfe6ea,#c8d3da)}
.footer-bar{top:4031px;height:60px;background:var(--footer-bar)}
.copyright{left:101px;top:22px;font-size:11px;color:var(--footer-text)}
.social{left:775px;top:20px;display:flex;align-items:center;gap:14px;font-size:11px;color:var(--footer-text)}
.social i{display:inline-block;width:12px;height:12px;border-radius:50%;background:#8f929c}
</style>
</head>
<body>

<header class="block site-header">
  <div class="abs brand"><div class="brand-mark"></div><span class="brand-name">KPV Datacore Solutions</span></div>
  <nav class="nav">
    <a style="left:641px">ABOUT US</a>
    <a style="left:755px">SERVICES</a>
    <a style="left:859px">WORK</a>
    <a style="left:944px">CAREERS</a>
    <a style="left:1047px">CONTACT</a>
  </nav>
</header>

<section class="block hero" role="img" aria-label="London bridge at night over the river, city lights reflected in the water">
  <h2 class="abs hero-title center">KPV Datacore Solutions</h2>
  <p class="abs hero-sub center">We are based in London and we are a recruitment company</p>
  <span class="abs btn">View our history</span>
</section>

<section class="block welcome">
  <h1>Welcome to KPV Datacore Solutions</h1>
  <p class="lead">Lorem Ipsum is simply dummy text of the printing and typesetting industry. Lorem Ipsum has been the industry's standard dummy text ever since the 1500s, when an unknown printer took a galley of type and scrambled it to make a type specimen book. It has survived not only five centuries, but also the leap into electronic typesetting, remaining essentially unchanged</p>
</section>

<section class="block services" style="height:480px">
  <h2 class="heading">Our Services</h2>
  <div class="rule"></div>
  <p class="lead">Lorem Ipsum is simply dummy text of the printing and typesetting industry. Lorem Ipsum has been the industry's standard dummy text ever since the 1500s, when an unknown printer took a galley of type and scrambled...</p>
  <div class="abs service" style="left:101px">
    <div class="service-photo" role="img" aria-label="Team of colleagues meeting around a desk" style="background:linear-gradient(135deg,#b9c2cc,#6f7f91 60%,#d8cfc4)"></div>
    <div class="service-title">SERVICES 01</div>
    <p class="service-text">Lorem Ipsum is simply dummy text of the printing and typesetting industry. Lorem Ipsum has been the industry's standard dummy text ever...</p>
  </div>
  <div class="abs service" style="left:445px">
    <div class="service-photo" role="img" aria-label="Young team working together at computers" style="background:linear-gradient(135deg,#8a9aa8,#4f6274 55%,#c9b8a6)"></div>
    <div class="service-title">SERVICES 02</div>
    <p class="service-text">Lorem Ipsum is simply dummy text of the printing and typesetting industry. Lorem Ipsum has been the industry's standard dummy text ever...</p>
  </div>
  <div class="abs service" style="left:791px">
    <div class="service-photo" role="img" aria-label="Group discussing a project around a laptop" style="background:linear-gradient(135deg,#5a6b80,#2f3e54 55%,#a48d7a)"></div>
    <div class="service-title">SERVICES 03</div>
    <p class="service-text">Lorem Ipsum is simply dummy text of the printing and typesetting industry. Lorem Ipsum has been the industry's standard dummy text ever...</p>
  </div>
</section>

<section class="block whatwedo" style="height:400px">
  <h2 class="heading">What We Do</h2>
  <div class="rule"></div>
  <p class="lead">Lorem Ipsum is simply dummy text of the printing and typesetting industry. Lorem Ipsum has been the industry's standard dummy text ever since the 1500s, when an unknown printer took a galley of type and scrambled...</p>
  <div class="abs feature" style="left:179px">
    <div class="feature-icon">
      <svg width="52" height="52" viewBox="0 0 52 52" fill="none" stroke="#fff" stroke-width="2.5"><rect x="8" y="30" width="8" height="14"/><rect x="22" y="22" width="8" height="22"/><rect x="36" y="14" width="8" height="30"/><path d="M8 22 L22 12 L30 16 L44 6"/></svg>
    </div>
    <div class="feature-title">Lorem Ipsum Simply</div>
    <p class="feature-text">Lorem Ipsum is simply dummy text of the printing and typesetting industry. Lorem Ipsum has been the industry...</p>
  </div>
  <div class="abs feature" style="left:485px">
    <div class="feature-icon">
      <svg width="52" height="52" viewBox="0 0 52 52" fill="none" stroke="#fff" stroke-width="2.5"><path d="M6 18 L26 6 L46 18 Z"/><path d="M12 22v16M20 22v16M32 22v16M40 22v16"/><path d="M6 42h40M4 46h44"/></svg>
    </div>
    <div class="feature-title">Lorem Ipsum Simply</div>
    <p class="feature-text">Lorem Ipsum is simply dummy text of the printing and typesetting industry. Lorem Ipsum has been the industry...</p>
  </div>
  <div class="abs feature" style="left:790px">
    <div class="feature-icon">
      <svg width="52" height="52" viewBox="0 0 52 52" fill="none" stroke="#fff" stroke-width="2.5"><circle cx="24" cy="28" r="18"/><circle cx="24" cy="28" r="11"/><circle cx="24" cy="28" r="4"/><path d="M24 28 L42 10 M36 10h6v6"/></svg>
    </div>
    <div class="feature-title">Lorem Ipsum Simply</div>
    <p class="feature-text">Lorem Ipsum is simply dummy text of the printing and typesetting industry. Lorem Ipsum has been the industry...</p>
  </div>
</section>

<section class="block about" role="img" aria-label="Blurred crowd of commuters walking through a city street">
  <h2 class="heading">About KPV Datacore Solutions</h2>
  <p class="lead">Lorem Ipsum is simply dummy text of the printing and typesetting industry. Lorem Ipsum has been the industry's standard dummy text ever since the 1500s, when an unknown printer took a galley of type and scrambled it to make a type specimen book. It has survived not only five centuries, but also the leap into electronic typesetting, remaining...</p>
  <span class="abs btn">View more history</span>
</section>

<section class="block posts" style="height:380px">
  <h2 class="heading">Latest Posts</h2>
  <div class="rule"></div>
  <p class="lead">Lorem Ipsum is simply dummy text of the printing and typesetting industry. Lorem Ipsum has been the industry's standard dummy text ever since the 1500s, when an unknown printer took a galley of type and scrambled...</p>
  <article class="abs post" style="left:101px">
    <div class="abs post-photo" role="img" aria-label="Woman working on a phone in an office" style="background:linear-gradient(135deg,#6c5a4c,#c9c5c0 55%,#8c97a3)"></div>
    <div class="abs post-body">
      <div class="post-title">Lorem Ipsum is simply dummy text of the printing</div>
      <div class="post-date">Posted on 27 march 2015</div>
      <p class="post-text">Lorem Ipsum is simply dummy text of the printing and typesetting industry. Lorem Ipsum has been the industry...</p>
    </div>
  </article>
  <article class="abs post" style="left:622px">
    <div class="abs post-photo" role="img" aria-label="Businessman leaning back in an office chair" style="background:linear-gradient(135deg,#d6d6d6,#8d8d8d 55%,#3f3f3f)"></div>
    <div class="abs post-body">
      <div class="post-title">Lorem Ipsum is simply dummy text of the printing</div>
      <div class="post-date">Posted on 27 march 2015</div>
      <p class="post-text">Lorem Ipsum is simply dummy text of the printing and typesetting industry. Lorem Ipsum has been the industry...</p>
    </div>
  </article>
  <div class="abs dots"><span class="dot on"></span><span class="dot"></span><span class="dot"></span></div>
</section>

<section class="block testimonial" role="img" aria-label="Man working on a laptop at a table by a bright window">
  <svg class="abs testimonial-panel" width="1200" height="538" viewBox="0 0 1200 538"><polygon points="0,0 545,0 805,538 0,538" fill="var(--red)"/></svg>
  <svg class="abs quote-mark" width="46" height="36" viewBox="0 0 46 36" fill="rgba(255,255,255,.6)"><path d="M0 36V20C0 9 6 2 17 0l2 5C12 7 9 11 9 16h9v20zM27 36V20C27 9 33 2 44 0l2 5c-7 2-10 6-10 11h9v20z"/></svg>
  <div class="abs quote">
    <p>Lorem Ipsum is simply dummy text of the printing and typesetting industry. Lorem Ipsum has been the industry's standard dummy text ever since the 1500s, when an unknown printer took a galley of type and scrambled.</p>
    <p>It to make a type specimen book. It has survived not only five centuries, but also the leap into electronic typesetting, remaining essentially unchanged...</p>
    <div class="quote-author">Marcus Hallow <span>- Business Man</span></div>
  </div>
  <div class="abs quote-dots"><span class="dot"></span><span class="dot"></span><span class="dot"></span></div>
</section>

<section class="block clients" style="height:340px">
  <h2 class="heading">Our Clients</h2>
  <div class="rule"></div>
  <p class="lead">Lorem Ipsum is simply dummy text of the printing and typesetting industry. Lorem Ipsum has been the industry's standard dummy text ever since the 1500s, when an unknown printer took a galley of type and scrambled...</p>
  <div class="abs client" style="left:160px;top:160px">Nordvale</div>
  <div class="abs client" style="left:340px;top:160px"><span class="client-dot"></span>Quillon</div>
  <div class="abs client" style="left:515px;top:160px">Peravis</div>
  <div class="abs client" style="left:690px;top:160px"><span class="client-dot"></span>Tarrow</div>
  <div class="abs client" style="left:865px;top:160px">Osmelle</div>
  <div class="abs client" style="left:160px;top:262px">Brindo</div>
  <div class="abs client" style="left:325px;top:262px"><span class="client-dot"></span>Lumetra</div>
  <div class="abs client" style="left:500px;top:262px">Vandry</div>
  <div class="abs client" style="left:665px;top:262px">Kestrow</div>
  <div class="abs client" style="left:870px;top:262px">Corvane</div>
</section>

<footer class="block site-footer">
  <div class="abs footer-brand">
    <div class="footer-mark"></div>
    <div class="footer-brand-name">KPV<br>Datacore Solutions</div>
  </div>
  <div class="abs footer-col" style="left:333px;width:340px">
    <div class="footer-h">Who we are?</div>
    <p class="footer-text">Lorem Ipsum is simply dummy text of the printing and typesetting industry. Lorem Ipsum has been the industry's standard dummy text ever since the 1500s, when an unknown printer took a galley of type and scrambled it...</p>
    <div class="read-more">Read more info <i></i></div>
  </div>
  <div class="abs footer-col" style="left:747px">
    <div class="footer-h">Welcome</div>
    <ul class="footer-links"><li>Home</li><li>About Us</li><li>Services</li><li>Work</li><li>Carrers</li><li>Contact</li></ul>
  </div>
  <div class="abs footer-col" style="left:916px">
    <div class="footer-h">Contact Info</div>
    <p class="footer-text" style="margin-top:14px;line-height:22px">12 Wharf Row<br>London, E2 7QT</p>
    <div class="map" role="img" aria-label="Small street map showing the office location"></div>
  </div>
</footer>
<div class="block footer-bar">
  <div class="abs copyright">© 2016, KPV Datacore Solutions. All rights reserved</div>
  <div class="abs social">Connect with our social network :<i></i><i></i><i></i><i></i><i></i></div>
</div>

</body>
</html>
```